Ridge Lass Crew (Flyer)

I want a flyer to advertise my service.
Details below, and logo's to use are attached.

A girls only after school program, 11-14yrs, as OSHC is no longer avail, dedicated to coaching & mentoring our girls into strong, independent young women.

The Brainchild of Rebecca Folwin, Ridge Lass Crew was created to address the growing demand for after school/school holiday supervision for kids moving from primary into high school, when OSHC ceases to exist.
With over 12 years experience mentoring and coaching young women in the corporate world, Bec decided to leave her role as a Director with Tarrant Trust, and follow her passion.
Bec, along with her sister Lorraine, who has over 10 years experience in local communities as a Youth Worker, and is also a qualified Enrolled Nurse, embarked on building a program designed to keep parents happy (by knowing their girls are safe) and dedicated to coaching and mentoring our girls into strong, independent young women.
Open every afternoon and during school holidays, we look to offer;
- Daily meditation
- Healthy snacks
- Dedicated homework time
- Organised group activity, led by qualified instructors (yoga, fitness class, soccer etc)
- Regular guests speakers, addressing issues/concerns for young people today
- SOCIAL MEDIA FREE ZONE

Located 87 Pelham Pde, Baulkham Hills (across from Crestmoor Day Clinic)
Open 3-6pm Monday to Friday

Facebook page: http://fb.example/ridgelasscrew
Email: info@ridgelasscrew.example.au
Mobile: 0455817396

Target Market(s)

Parents of teenage girls, teenage girls 11-14 years

Industry/Entity Type

School

Font styles to use
Sans Serif

Colors
b768aa
e667a6

Requirements
Must have
• What progam is - see brief
• Who runs it
Should not have
• Not be too busy, not overly mature images

```html
<!DOCTYPE html>
<html lang="en">
<head>
<meta charset="utf-8">
<title>Ridge Lass Crew – After School Program Flyer</title>
<link href="https://fonts.googleapis.com/css2?family=Cabin:wght@400;600;700&family=Cinzel:wght@700&family=Philosopher:wght@700&family=Libre+Baskerville:ital@1&family=Roboto+Condensed:wght@300;400&display=swap" rel="stylesheet">
<style>
  :root {
    --purple: #b768aa;
    --purple-box: rgba(183, 104, 170, 0.95);
    --pink: #e667a6;
    --logo-pink: #e0457f;
    --ink: #1d1a1c;
    --white: #ffffff;
    --icon-purple: #b768aa;
  }
  * { margin: 0; padding: 0; box-sizing: border-box; }
  html, body { width: 848px; height: 1200px; overflow: hidden; background: var(--white); }
  .flyer { position: relative; width: 848px; height: 1200px; overflow: hidden; font-family: "Cabin", sans-serif; color: var(--ink); }

  .hero-photo {
    position: absolute; left: 0; top: 0; width: 848px; height: 470px;
    background:
      radial-gradient(circle at 35% 25%, #c8423f 0, rgba(200,66,63,0) 28%),
      radial-gradient(circle at 95% 20%, #c9303a 0, rgba(201,48,58,0) 30%),
      radial-gradient(circle at 45% 60%, #2f6f6a 0, rgba(47,111,106,0) 35%),
      radial-gradient(circle at 20% 85%, #d9b54a 0, rgba(217,181,74,0) 30%),
      linear-gradient(160deg, #3a2a3a, #4a3a36 50%, #2b2a2c);
  }

  .logo-card {
    position: absolute; left: 34px; top: 36px; width: 258px; height: 360px;
    background: var(--white);
    display: flex; flex-direction: column; align-items: center; justify-content: center; gap: 14px;
  }
  .logo-dot { width: 40px; height: 40px; border-radius: 50%; background: var(--logo-pink); }
  .logo-name {
    font-family: "Philosopher", sans-serif; font-weight: 700; font-size: 46px; line-height: 1.05;
    color: var(--logo-pink); text-align: center;
  }

  .age-panel {
    position: absolute; left: 412px; top: 62px; width: 388px; height: 328px;
    background: var(--purple-box); border-radius: 16px; text-align: center;
  }
  .age-panel .headline { margin-top: 40px; font-size: 46px; font-weight: 600; letter-spacing: 1px; }
  .age-panel .subline { margin-top: 4px; font-size: 27px; letter-spacing: 1px; white-space: nowrap; }
  .age-panel .ages { margin-top: 6px; font-size: 66px; font-weight: 700; color: var(--white); }
  .age-panel .note { margin-top: 8px; font-size: 21px; font-weight: 700; }

  .intro-band {
    position: absolute; left: 0; top: 470px; width: 848px; height: 175px;
    background: var(--pink); text-align: center;
  }
  .intro-band .creator { margin-top: 10px; margin-left: 12px; font-family: "Philosopher", sans-serif; font-size: 29px; }
  .intro-band .program { font-family: "Philosopher", sans-serif; font-size: 29px; margin-top: 2px; }
  .intro-band .mission {
    margin-top: 12px; margin-left: 58px; width: 760px; font-family: "Cinzel", sans-serif;
    font-variant: small-caps; font-size: 22px; line-height: 36px; letter-spacing: 3px;
    color: var(--white); text-shadow: 0 0 2px rgba(0,0,0,0.6);
  }

  .offer-section {
    position: absolute; left: 0; top: 644px; width: 848px; height: 443px; background: var(--purple);
  }
  .offer-title {
    position: absolute; left: 0; width: 816px; top: 14px; text-align: center;
    font-family: "Cinzel", sans-serif; font-variant: small-caps; font-size: 36px; color: var(--ink);
  }
  .offer-list { list-style: none; position: absolute; left: 26px; top: 64px; }
  .offer-list li {
    display: flex; align-items: flex-start; gap: 12px; height: 42px;
    font-family: "Libre Baskerville", serif; font-style: italic; font-size: 22px; color: var(--white);
  }
  .offer-list li.two-line { height: 82px; line-height: 40px; margin-top: -8px; }
  .offer-list svg { flex: none; margin-top: 6px; }
  .hours { position: absolute; left: 0; top: 358px; width: 848px; text-align: center; font-size: 33px; }
  .hours .days { display: block; margin-left: -60px; color: var(--white); line-height: 1.25; }

  .contact-bar {
    position: absolute; left: 0; top: 1087px; width: 848px; height: 113px; background: var(--pink);
    font-family: "Roboto Condensed", sans-serif; color: var(--white); font-size: 17px;
  }
  .contact-item { position: absolute; }
  .contact-icon { position: absolute; }
  .email-text { left: 79px; top: 14px; line-height: 26px; }
  .social-text { left: 73px; top: 76px; }
  .phone-text { left: 394px; top: 28px; line-height: 26px; }
  .phone-text strong { font-weight: 400; }
  .address-text { left: 651px; top: 26px; line-height: 25px; }
  .address-text small { font-size: 13px; }
</style>
</head>
<body>
<div class="flyer">
  <div class="hero-photo" role="img" aria-label="Photo of school supplies: red sneakers, notebooks, pencils and a phone on a woven mat"></div>

  <div class="logo-card">
    <div class="logo-dot"></div>
    <div class="logo-name">Ridge Lass<br>Crew</div>
  </div>

  <div class="age-panel">
    <div class="headline">A GIRLS ONLY</div>
    <div class="subline">AFTER SCHOOL PROGRAM</div>
    <div class="ages">11-14yrs</div>
    <div class="note">as OSHC is no longer available</div>
  </div>

  <section class="intro-band">
    <div class="creator">The Brainchild of Rebecca Folwin</div>
    <div class="program">Ridge Lass Crew</div>
    <div class="mission">Dedicated to Coaching &amp; Mentoring Our Girls into Strong, Independent Young women</div>
  </section>

  <section class="offer-section">
    <h2 class="offer-title">We look to offer</h2>
    <ul class="offer-list">
      <li><svg width="16" height="16" viewBox="0 0 16 16"><circle cx="8" cy="8" r="6.5" fill="none" stroke="#fff" stroke-width="1.6"/><path d="M5 8.2l2 2 4-4" fill="none" stroke="#fff" stroke-width="1.6"/></svg>Daily meditation</li>
      <li><svg width="16" height="16" viewBox="0 0 16 16"><circle cx="8" cy="8" r="6.5" fill="none" stroke="#fff" stroke-width="1.6"/><path d="M5 8.2l2 2 4-4" fill="none" stroke="#fff" stroke-width="1.6"/></svg>Healthy snacks</li>
      <li><svg width="16" height="16" viewBox="0 0 16 16"><circle cx="8" cy="8" r="6.5" fill="none" stroke="#fff" stroke-width="1.6"/><path d="M5 8.2l2 2 4-4" fill="none" stroke="#fff" stroke-width="1.6"/></svg>Dedicated homework time</li>
      <li class="two-line"><svg width="16" height="16" viewBox="0 0 16 16" style="margin-top:14px"><circle cx="8" cy="8" r="6.5" fill="none" stroke="#fff" stroke-width="1.6"/><path d="M5 8.2l2 2 4-4" fill="none" stroke="#fff" stroke-width="1.6"/></svg><span>Organised group activity, led by qualified instructors<br>(yoga, fitness class, soccer etc.)</span></li>
      <li><svg width="16" height="16" viewBox="0 0 16 16"><circle cx="8" cy="8" r="6.5" fill="none" stroke="#fff" stroke-width="1.6"/><path d="M5 8.2l2 2 4-4" fill="none" stroke="#fff" stroke-width="1.6"/></svg>Regular guests speakers</li>
      <li><svg width="16" height="16" viewBox="0 0 16 16"><circle cx="8" cy="8" r="6.5" fill="none" stroke="#fff" stroke-width="1.6"/><path d="M5 8.2l2 2 4-4" fill="none" stroke="#fff" stroke-width="1.6"/></svg>SOCIAL MEDIA FREE ZONE</li>
    </ul>
    <p class="hours">Open every afternoon and during school holidays<span class="days">3-6pm Monday to Friday</span></p>
  </section>

  <footer class="contact-bar">
    <svg class="contact-icon" style="left:18px;top:16px" width="40" height="40" viewBox="0 0 40 40"><circle cx="20" cy="20" r="20" fill="var(--icon-purple)"/><rect x="11" y="13" width="18" height="13" rx="2" fill="#fff"/><path d="M11.5 14l8.5 7 8.5-7" fill="none" stroke="var(--icon-purple)" stroke-width="1.8"/></svg>
    <div class="contact-item email-text">e-Mail us<br>info@ridgelasscrew.example.au</div>
    <svg class="contact-icon" style="left:22px;top:76px" width="26" height="26" viewBox="0 0 26 26"><rect width="26" height="26" rx="4" fill="#3b5a98"/></svg>
    <div class="contact-item social-text">http://fb.example/ridgelasscrew</div>

    <svg class="contact-icon" style="left:324px;top:27px" width="52" height="52" viewBox="0 0 52 52"><circle cx="26" cy="26" r="26" fill="var(--icon-purple)"/><rect x="19" y="13" width="14" height="26" rx="2.5" fill="none" stroke="#fff" stroke-width="2"/><line x1="19" y1="34" x2="33" y2="34" stroke="#fff" stroke-width="1.5"/><circle cx="26" cy="36.5" r="1.2" fill="#fff"/></svg>
    <div class="contact-item phone-text">Call Us Now<br><strong>0455817396</strong></div>

    <svg class="contact-icon" style="left:574px;top:27px" width="52" height="52" viewBox="0 0 52 52"><circle cx="26" cy="26" r="26" fill="var(--icon-purple)"/><path d="M26 39c-6-8-9-12-9-16a9 9 0 0118 0c0 4-3 8-9 16z" fill="#fff"/><circle cx="26" cy="23" r="3.5" fill="var(--icon-purple)"/></svg>
    <div class="contact-item address-text">87 Pelham Pde,<br>Baulkham Hills<br><small>(across from Crestmoor Day Clinic)</small></div>
  </footer>
</div>
</body>
</html>
```